Dental office stationary (letterhead, envelopes), business cards, presentation folders

Nothing too dental outside of the logo. I will need all stationary, presentation folders, business cards. Would prefer to stay in the colors of the logo

Gordon Patel, DDS
Bright Haven Dental Implant Center
555-318-2790
info@brighthavendental.example
4817 NW Maple Crest Rd Unit B
Stuart, FL 00000

Also need appointment date and time
And cancellation policy
I want it to say “kindly ask for
A 48hr cancellation policy to avoid incurring a cancellation fee”

Industry/Entity Type

Dental

Colors
0054AA
0677BA
7BADD7
CADEEF
E8F1F8

Requirements
Must have
• Name of your office, name of doctor, address, phone number
Should not have
• Too much tooth/dental. Only the tooth in logo

```html
<!DOCTYPE html>
<html lang="en">
<head>
<meta charset="UTF-8">
<title>Bright Haven Dental Implant Center – Business Card</title>
<link href="https://fonts.googleapis.com/css2?family=Roboto:ital,wght@0,400;0,700;1,400;1,700&display=swap" rel="stylesheet">
<style>
  :root {
    --page-bg: #e9ecef;
    --card-bg: #1f1f21;
    --ink-light: #f2f2f2;
    --brand-blue: #1ab2e8;
    --brand-teal: #17b99a;
    --card-shadow: rgba(0, 0, 0, 0.25);
  }
  * { box-sizing: border-box; margin: 0; padding: 0; }
  html, body { width: 1200px; height: 900px; overflow: hidden; }
  body {
    background: var(--page-bg);
    font-family: "Roboto", Arial, sans-serif;
    display: flex;
    flex-direction: column;
    align-items: center;
    justify-content: center;
    gap: 40px;
  }
  .business-card {
    position: relative;
    width: 700px;
    height: 400px;
    background: var(--card-bg);
    box-shadow: 0 12px 30px var(--card-shadow);
    overflow: hidden;
  }

  /* Front */
  .card-front .brand-name {
    position: absolute;
    right: 56px;
    bottom: 56px;
    display: flex;
    align-items: center;
    gap: 12px;
  }
  .brand-dot {
    width: 16px; height: 16px;
    border-radius: 50%;
    background: var(--brand-teal);
  }
  .brand-text {
    font-size: 34px;
    font-weight: 700;
    letter-spacing: 2px;
    text-transform: uppercase;
    color: var(--brand-blue);
  }

  /* Back */
  .card-back .brand-name {
    position: absolute;
    left: 48px;
    top: 44px;
    display: flex;
    align-items: center;
    gap: 10px;
  }
  .card-back .brand-text { font-size: 26px; }
  .card-back .brand-dot { width: 12px; height: 12px; }

  .office-address {
    position: absolute;
    left: 48px;
    top: 122px;
    font-style: italic;
    font-size: 17px;
    line-height: 1.35;
    color: var(--ink-light);
  }
  .contact-list {
    position: absolute;
    left: 48px;
    top: 222px;
    list-style: none;
    font-style: italic;
    font-size: 17px;
    line-height: 1.55;
    color: var(--ink-light);
  }
  .contact-item { display: flex; align-items: center; gap: 10px; }
  .contact-icon { width: 15px; height: 15px; flex: none; }
  .web-accent { color: var(--brand-teal); }

  .doctor-block {
    position: absolute;
    right: 70px;
    bottom: 88px;
    text-align: right;
  }
  .doctor-name {
    font-size: 22px;
    font-weight: 700;
    font-style: italic;
    color: var(--brand-blue);
  }
  .practice-name {
    margin-top: 4px;
    font-size: 16px;
    font-style: italic;
    color: var(--ink-light);
  }
  .accent-bar {
    position: absolute;
    right: 40px;
    bottom: 70px;
    width: 16px;
    height: 60px;
    background: var(--brand-teal);
  }
</style>
</head>
<body>

  <section class="business-card card-front" aria-label="Business card front">
    <div class="brand-name">
      <span class="brand-dot"></span>
      <span class="brand-text">Bright Haven</span>
    </div>
  </section>

  <section class="business-card card-back" aria-label="Business card back">
    <div class="brand-name">
      <span class="brand-dot"></span>
      <span class="brand-text">Bright Haven</span>
    </div>

    <address class="office-address">
      4817 NW Maple Crest Rd Unit B<br>
      Stuart, FL 00000
    </address>

    <ul class="contact-list">
      <li class="contact-item">
        <svg class="contact-icon" viewBox="0 0 16 16" aria-hidden="true">
          <path fill="#17b99a" d="M3.5 1.5l2.5 0 1 3.5-1.6 1.2a8 8 0 0 0 4.4 4.4l1.2-1.6 3.5 1v2.5a1.5 1.5 0 0 1-1.5 1.5A12.5 12.5 0 0 1 2 3a1.5 1.5 0 0 1 1.5-1.5z"/>
        </svg>
        555-318-2790
      </li>
      <li class="contact-item">
        <svg class="contact-icon" viewBox="0 0 16 16" aria-hidden="true">
          <rect x="1" y="3" width="14" height="10" rx="1" fill="#17b99a"/>
          <path d="M1.5 3.5l6.5 5 6.5-5" fill="none" stroke="#1f1f21" stroke-width="1.4"/>
        </svg>
        info@brighthavendental.example
      </li>
      <li class="contact-item">
        <svg class="contact-icon" viewBox="0 0 16 16" aria-hidden="true">
          <circle cx="8" cy="8" r="7" fill="#17b99a"/>
          <path d="M1 8h14M8 1c-2.5 2.5-2.5 11.5 0 14M8 1c2.5 2.5 2.5 11.5 0 14" fill="none" stroke="#1f1f21" stroke-width="1.1"/>
        </svg>
        <span>www.<span class="web-accent">brighthavendental</span>.example</span>
      </li>
    </ul>

    <div class="doctor-block">
      <p class="doctor-name">Gordon Patel, DDS</p>
      <p class="practice-name">Bright Haven Dental Implant Center</p>
    </div>
    <div class="accent-bar"></div>
  </section>

</body>
</html>
```